Conference flyer

We need a flyer for a conference for the defence industry. The attached has been updated with new information using last years flyer. We would like something new and fresh. Please note the theme of the conference is 'a global environment'.

The final design should reflect the defence industry and manufacturing.

Industry/Entity Type

Defence

```html
<!DOCTYPE html>
<html lang="en">
<head>
<meta charset="utf-8">
<title>Defence Trade Controls Annual Conference</title>
<link href="https://fonts.googleapis.com/css2?family=Open+Sans:wght@400;600;700&display=swap" rel="stylesheet">
<style>
  :root {
    --backdrop: #1e1e1e;
    --paper: #ffffff;
    --navy: #1c2a58;
    --title-blue: #2b3894;
    --label-blue: #2a55a6;
    --link-blue: #3b80c6;
    --ink: #1a1a1a;
    --table-head: #d6d7d9;
    --table-row: #e5e6e7;
    --table-line: #f4f4f4;
  }
  * { margin: 0; padding: 0; box-sizing: border-box; }
  html, body {
    width: 913px; height: 1200px; overflow: hidden;
    background: var(--backdrop);
    font-family: "Open Sans", Arial, sans-serif;
    color: var(--ink);
  }
  .flyer {
    position: absolute; left: 0; top: 12px;
    width: 913px; height: 1176px;
    background: var(--paper);
    overflow: hidden;
  }
  .masthead {
    position: absolute; left: 0; top: 0; width: 913px; height: 175px;
    background: linear-gradient(180deg, #3f5fb3 0%, #8fa7d8 10%, #eef2fa 22%, #f6f8fc 60%, #c9d5ee 85%, #4a6ab8 100%);
  }
  .masthead-art { position: absolute; inset: 0; }
  .masthead h1 {
    position: absolute; left: 0; right: 0; top: 30px;
    text-align: center; color: var(--title-blue);
    font-weight: 700; line-height: 58px; font-size: 47px; letter-spacing: 0.5px;
  }
  .masthead h1 span { display: block; }
  .section-bar {
    position: absolute; left: 13px; width: 887px; height: 41px;
    background: var(--navy); color: #fff;
    font-weight: 700; font-size: 19px; line-height: 41px; padding-left: 14px;
  }
  .section-bar small { font-size: 13px; }
  .bar-prices { top: 197px; }
  .bar-info { top: 410px; padding-left: 26px; }
  .prices {
    position: absolute; left: 16px; top: 250px; width: 882px;
    border-collapse: collapse; font-size: 14px; text-align: center;
  }
  .prices th {
    background: var(--table-head); font-weight: 400; font-size: 15px; height: 34px;
    border-right: 2px solid var(--table-line);
  }
  .prices th small { font-size: 9px; }
  .prices td {
    background: var(--table-row); height: 36px;
    border-right: 2px solid var(--table-line); border-top: 2px solid var(--table-line);
  }
  .prices td.item { font-weight: 600; font-size: 13px; width: 186px; }
  .prices th:last-child, .prices td:last-child { border-right: none; }
  .info-row { position: absolute; left: 22px; width: 880px; display: flex; }
  .info-row dt {
    width: 292px; flex: none; color: var(--label-blue);
    font-weight: 700; font-size: 18px; line-height: 23.5px;
  }
  .info-row dd { flex: 1; font-size: 15px; line-height: 23.5px; white-space: nowrap; }
  .info-row a { color: var(--link-blue); text-decoration: none; }
</style>
</head>
<body>
<main class="flyer">
  <header class="masthead">
    <svg class="masthead-art" role="img" aria-label="Globe with network lines in blue tones" width="913" height="175" viewBox="0 0 913 175">
      <g stroke="#ffffff" stroke-opacity="0.6" stroke-width="1.5" fill="none">
        <path d="M0 150 L300 175"/>
        <path d="M600 175 L913 120"/>
        <path d="M700 0 L913 60"/>
      </g>
    </svg>
    <h1><span>DEFENCE TRADE CONTROLS</span><span>ANNUAL CONFERENCE</span></h1>
  </header>

  <div class="section-bar bar-prices">CONFERENCE PRICES <small>(ALL PRICES INCLUDE GST)</small></div>

  <table class="prices">
    <tr>
      <th></th>
      <th>Super Earlybird <small>(prior 31 Dec 14)</small></th>
      <th>Earlybird <small>(prior 31 Mar 15)</small></th>
      <th>Standard Pricing</th>
    </tr>
    <tr><td class="item">Conference Only</td><td>$1,095</td><td>$1,095</td><td>$1,095</td></tr>
    <tr><td class="item">Training Module</td><td>$1,095</td><td>$1,095</td><td>$1,095</td></tr>
    <tr><td class="item">Training Module</td><td>$1,095</td><td>$1,095</td><td>$1,095</td></tr>
  </table>

  <div class="section-bar bar-info">GENERAL INFORMATION</div>

  <dl>
    <div class="info-row" style="top:478px"><dt>Conference Venue:</dt><dd>Harbourline Melbourne 14 Riverside Lane, Southbank, 3006<br>Ph: (03) 9000 4521</dd></div>
    <div class="info-row" style="top:538px"><dt>Registration Fee Includes:</dt><dd>Entrance to the conference, refreshments, lunch, reception event on the first<br>evening.</dd></div>
    <div class="info-row" style="top:593px"><dt>Dress code:</dt><dd>Business attire.</dd></div>
    <div class="info-row" style="top:641px"><dt>Accommodation and Travel:</dt><dd>Travel and accommodation are not included in the conference fees.<br>We do not refund airfares or hotel expenses if the event is cancelled.<br>Contact Harbourline Melbourne for competitive prices.</dd></div>
    <div class="info-row" style="top:729px"><dt>Sponsorship Opportunities:</dt><dd>Sponsoring the Defence Trade Controls Conference 2015 is a fantastic<br>way ofraising your company’s profile within this market and creating greater<br>awareness of your brand. Join us at the Defence Trade Controls Conference<br>to promote new and existing products and service offerings in a high profile<br>way amongst a select group of other sponsors and exhibitors.<br><a href="#">Contact us at conference@dtcevents.example to find out more information.</a></dd></div>
    <div class="info-row" style="top:886px"><dt>Early bird prices:</dt><dd>Early bird prices only apply to conference registrations and post conference<br>training module registrations that have been paid in full by midnight 1of the<br>date the earlybird closes</dd></div>
    <div class="info-row" style="top:963px"><dt>Cancellation &amp; Substitution<br>policy:</dt><dd>Cancellations must be advised in writing at least 30 days prior to the event.<br>An administration fee of $250 (inc. GST) will be incurred for all cancellations.<br>A refund will not be given within 30 days of the event. If a registered attendee<br>is unable to attend, a replacement attendee is welcome.</dd></div>
    <div class="info-row" style="top:1071px"><dt>Payment Terms:</dt><dd>Payment must be made prior to the event or admittance will not be permitted.</dd></div>
    <div class="info-row" style="top:1120px"><dt>Electronic Ticket:</dt><dd>You will recieve an electronic ticket when you register online - tickets must be<br>presented upon entry.</dd></div>
  </dl>
</main>
</body>
</html>
```